Scrum Master & Agile IT Coach Needing Business Website

Hello, my name is Joel Brandt
I am a project manger, scrum master, & agile coach. I work with IT development teams on major projects for Summit 300 companies . My project management business has a website and can be found here: www.tk-steadfast.example

I have launched a new company, ALL focused on IT Agile Coaching, I am looking to have a website created for my new company - the name of the new company is: Q's and V's - Agile IT Coaching and Training.
I have a logo and it is provided in the materials. I like to logo; I am open to different color pallets.

The website will have a total of 7 pages; I have content for 5 of the 7 pages prepared; the other 2 pages will say under construction.

Page 1 Who am I, What I do, My Experience
Demonstrated experience and progression from Scrum Master to
Program Manager to Coach

Page 2 Q's & V's - Agile Team Coaching
teams working major IT projects, multiple months/years

Page 3 Coaching @ the Team Level

Page 4 Coaching @ the Program Level ; LIMBr ART level

Pages 5 -6 Under Construction

Page 7 Presentations, Slide Decks, Reference Materials

Mentors Nook need to have this highlighted somewhere Monthly Blog
Updates

Industry/Entity Type

IT development

Coding

Coded - Design and coding required

Number of Pages Required

5+ page

Requirements
Must have
• the website must be bold - I want those who visit to remember coming to my coaching site
Nice to have
• nice to have will be a modern / futuristic website; I work with IT developers, I want a website they will like
Should not have
• should not be stiff - it should be professional but fun

```html
<!DOCTYPE html>
<html lang="en">
<head>
<meta charset="utf-8">
<title>Q's &amp; V's – Agile IT Coaching &amp; Training</title>
<link href="https://fonts.googleapis.com/css2?family=Inter:wght@400;500;600;700&family=Poppins:wght@600;700;800&display=swap" rel="stylesheet">
<style>
:root{
  --navy:#0d2a4e;
  --ink:#1b2b3f;
  --text:#3d4b5c;
  --blue:#1579c8;
  --sky:#1e8fe0;
  --deep:#12488c;
  --hero-a:#061b3c;
  --hero-b:#0d3f80;
  --line:#d9dee5;
  --foot:#ececee;
  --white:#ffffff;
}
*{box-sizing:border-box;margin:0;padding:0}
html,body{width:1200px;height:3972px;overflow:hidden}
body{position:relative;background:var(--white);font-family:"Inter",sans-serif;color:var(--text)}
a{color:inherit}
.abs{position:absolute}

/* top bar */
.topbar{top:0;left:0;width:1200px;height:86px}
.brand{display:flex;align-items:center;gap:12px;font-family:"Poppins",sans-serif;font-weight:800;font-size:30px;color:var(--deep);letter-spacing:.5px}
.brand-mark{width:22px;height:22px;background:var(--sky);border-radius:3px}
.topbar .brand{position:absolute;left:93px;top:20px}
.contact-item{position:absolute;top:30px;display:flex;align-items:center;gap:12px;font-size:15px;color:var(--navy)}
.contact-item svg{width:22px;height:22px}
.contact-item.email{left:532px}
.contact-item.phone{left:806px;font-weight:600;font-size:16px}
.divider-v{position:absolute;top:34px;width:2px;height:18px;background:var(--blue)}
.socials{position:absolute;left:1014px;top:36px;display:flex;gap:26px}
.socials span{width:12px;height:12px;border-radius:50%;background:var(--blue)}

/* nav */
.nav{top:86px;left:0;width:1200px;height:57px;background:var(--blue)}
.nav a{position:absolute;top:21px;font-size:13.5px;font-weight:600;color:var(--white);text-decoration:none;text-transform:uppercase;letter-spacing:.2px}
.nav .active::after{content:"";position:absolute;left:50%;margin-left:-10px;bottom:-19px;width:20px;height:3px;background:var(--white)}

/* hero */
.hero{top:143px;left:0;width:1200px;height:560px;overflow:hidden}
.hero-art{position:absolute;inset:0;background:
  radial-gradient(circle at 76% 38%, rgba(72,200,255,.85) 0, rgba(30,120,220,.55) 14%, rgba(13,63,128,0) 30%),
  radial-gradient(ellipse at 80% 75%, rgba(160,120,100,.45) 0, rgba(13,63,128,0) 28%),
  linear-gradient(100deg,var(--hero-a) 0%,var(--hero-b) 60%,#0a2f63 100%)}
.hero h1{position:absolute;left:93px;top:150px;font-family:"Poppins",sans-serif;font-weight:800;font-size:58px;color:var(--white);letter-spacing:1px;line-height:1}
.hero .tagline{position:absolute;left:93px;top:212px;font-family:"Poppins",sans-serif;font-weight:600;font-size:23px;color:var(--white)}
.hero .rule{position:absolute;left:93px;top:258px;width:78px;height:2px;background:rgba(255,255,255,.55)}
.hero .rule::after{content:"";position:absolute;left:28px;top:-1px;width:22px;height:4px;background:var(--sky)}
.btn{display:flex;align-items:center;justify-content:center;gap:12px;background:var(--blue);color:var(--white);font-weight:700;font-size:14.5px;letter-spacing:.6px;text-transform:uppercase;text-decoration:none;border-radius:3px}
.btn svg{width:22px;height:14px}
.hero .btn{position:absolute;left:93px;top:300px;width:189px;height:47px}
.hero-edge{position:absolute;left:0;top:586px;width:1200px;height:117px}

/* about */
.photo-frame{left:108px;top:776px;width:365px;height:488px;border:5px solid var(--blue)}
.photo{left:93px;top:793px;width:366px;height:518px;border-bottom-left-radius:48px;background:linear-gradient(160deg,#5f5a54 0%,#7a6450 45%,#3a2f2a 100%)}
.about{left:529px;top:770px;width:580px}
.about h2{font-family:"Poppins",sans-serif;font-weight:700;font-size:33px;line-height:41px;color:var(--navy);text-transform:uppercase}
.about .lead{margin-top:24px;font-size:16.5px;line-height:31px;color:var(--ink);font-weight:500}
.about p{margin-top:16px;font-size:16px;line-height:31px}
.about p + p{margin-top:31px}
.signature{margin-top:26px;border-left:4px solid var(--blue);padding-left:14px}
.signature strong{display:block;font-size:15.5px;letter-spacing:3px;color:var(--navy);text-transform:uppercase;font-weight:700;line-height:22px}
.signature span{font-size:16px;color:var(--ink)}

.section-title{position:absolute;left:0;width:1200px;text-align:center;font-family:"Poppins",sans-serif;font-weight:700;font-size:21px;color:var(--navy);text-transform:uppercase}

/* designations */
.badges{left:93px;top:1483px;width:1014px;height:142px;border-top:2px solid var(--line);border-bottom:2px solid var(--line);display:grid;grid-template-columns:195px 218px 194px 211px 196px}
.badges .cell{display:flex;align-items:center;justify-content:center;border-right:2px solid var(--line)}
.badges .cell:last-child{border-right:0}
.badges svg{width:132px;height:124px}

.profiles{left:93px;top:1698px;width:1020px;display:grid;grid-template-columns:347px 345px 320px}
.profile h3{display:flex;align-items:center;gap:8px;font-size:16.5px;font-weight:600;letter-spacing:.6px;color:var(--navy)}
.profile h3 svg{width:15px;height:15px}
.profile a{display:block;margin-top:20px;font-size:16px;line-height:28px;color:var(--deep)}

/* roles */
.roles{left:310px;top:1956px;width:600px;height:145px}
.roles .vline{position:absolute;left:281px;top:5px;width:2px;height:136px;background:var(--deep)}
.roles .hline{position:absolute;left:55px;top:67px;width:451px;height:2px;background:var(--deep)}
.role{position:absolute;display:flex;gap:16px;font-size:16px;line-height:24px;color:var(--text)}
.role svg{flex:none;width:38px;height:32px;margin-top:4px}

/* experience */
.exp-band{left:0;top:2180px;width:1200px;height:1160px}
.exp-title{top:2302px;color:var(--white);font-size:33px}
.card{position:absolute;top:2398px;width:316px;height:848px}
.card-body{position:absolute;left:0;top:31px;width:316px;height:817px;background:var(--white);border-radius:158px}
.card-hex{position:absolute;left:100px;top:0;width:116px;height:120px}
.card h3{position:absolute;left:20px;top:158px;width:276px;text-align:center;font-size:16px;line-height:27px;font-weight:700;color:var(--navy);text-transform:uppercase}
.card h3::after{content:"";display:block;width:40px;height:3px;margin:12px auto 0;background:linear-gradient(90deg,var(--navy) 0 30%,var(--sky) 30% 70%,var(--navy) 70%)}
.card ul{position:absolute;left:20px;top:236px;width:280px;list-style:none}
.card li{display:flex;gap:14px;font-size:16.5px;line-height:28px;color:var(--text);margin-bottom:22px}
.card li svg{flex:none;width:28px;height:24px;margin-top:6px}

/* cta */
.cta{left:93px;top:3392px;border-left:4px solid var(--deep);padding-left:12px}
.cta h2{font-family:"Poppins",sans-serif;font-weight:700;font-size:35px;line-height:41px;color:var(--navy);text-transform:uppercase;margin-top:-4px}
.cta-btn{left:877px;top:3402px;width:191px;height:48px;box-shadow:0 8px 14px rgba(21,121,200,.3)}

/* footer */
.footer-bg{left:0;top:3500px;width:1200px;height:472px}
.footer-brand{left:93px;top:3645px}
.social-label{left:93px;top:3728px;display:flex;align-items:center;gap:20px;font-size:16.5px;font-weight:600;color:var(--navy);letter-spacing:.5px}
.social-label span{width:11px;height:11px;border-radius:50%;background:var(--blue)}
.copy{left:93px;top:3802px;font-size:15px;line-height:26px;color:var(--text)}
.foot-col h4{font-size:16px;font-weight:700;letter-spacing:.6px;color:var(--navy);text-transform:uppercase;margin-bottom:16px}
.sitemap{left:507px;top:3637px}
.sitemap li{list-style:none;font-size:15.5px;line-height:35.5px;color:var(--text)}
.contacts{left:817px;top:3637px;width:290px}
.contacts .row{display:flex;gap:18px;font-size:15.5px;line-height:28px;color:var(--text);margin-bottom:29px}
.contacts .row svg{flex:none;width:16px;height:16px;margin-top:6px}
</style>
</head>
<body>

<svg width="0" height="0" style="position:absolute">
  <defs>
    <symbol id="ico-laptop" viewBox="0 0 38 32">
      <rect x="11" y="3" width="22" height="17" fill="none" stroke="#12488c" stroke-width="2.6"/>
      <rect x="15" y="7" width="14" height="9" fill="#1e8fe0"/>
      <path d="M3 27h32M3 27l4-5h4" fill="none" stroke="#12488c" stroke-width="2.6"/>
      <path d="M7 13v14" stroke="#1e8fe0" stroke-width="2.6"/>
    </symbol>
    <symbol id="ico-arrow" viewBox="0 0 22 14">
      <path d="M1 7h19M14 1l6 6-6 6" fill="none" stroke="#fff" stroke-width="2"/>
    </symbol>
  </defs>
</svg>

<!-- top bar -->
<header class="abs topbar">
  <div class="brand"><span class="brand-mark"></span>Q's &amp; V's</div>
  <div class="contact-item email">
    <svg viewBox="0 0 22 22"><rect x="2" y="5" width="18" height="13" rx="1.5" fill="none" stroke="#1579c8" stroke-width="1.8"/><path d="M2 6l9 7 9-7" fill="none" stroke="#1579c8" stroke-width="1.8"/></svg>
    qsandvs@mail.example
  </div>
  <span class="divider-v" style="left:778px"></span>
  <div class="contact-item phone">
    <svg viewBox="0 0 22 22"><path d="M5 3l4 1 1 4-2 2c1 2.5 3 4.5 5 5l2-2 4 1 1 4-2 2C9 20 2 13 2 5z" fill="none" stroke="#1579c8" stroke-width="1.7"/></svg>
    555-210-4478
  </div>
  <span class="divider-v" style="left:982px"></span>
  <div class="socials"><span></span><span></span><span></span></div>
</header>

<nav class="abs nav">
  <a class="active" style="left:134px">Who am I</a>
  <a style="left:267px">Q's &amp; V's</a>
  <a style="left:392px">The Team Level</a>
  <a style="left:566px">The Program Level</a>
  <a style="left:774px">Presentations</a>
  <a style="left:950px">Monthly Blog</a>
</nav>

<!-- hero -->
<section class="abs hero">
  <div class="hero-art" role="img" aria-label="Hand holding a glowing digital globe of technology icons on a deep blue background"></div>
  <h1>Q'S &amp; V'S</h1>
  <p class="tagline">Agile IT Coaching &amp; Training.</p>
  <span class="rule"></span>
  <a class="btn">Get in touch <svg><use href="#ico-arrow"/></svg></a>
  <svg class="hero-edge" viewBox="0 0 1200 117" preserveAspectRatio="none">
    <polygon points="0,14 56,14 96,93 1092,93 1140,14 1200,14 1200,117 0,117" fill="#ffffff"/>
    <polygon points="100,82 1090,82 1082,93 106,93" fill="#06183a"/>
    <polyline points="0,5 62,5 102,78 1090,78 1136,5 1200,5" fill="none" stroke="#1e8fe0" stroke-width="9"/>
  </svg>
</section>

<!-- about -->
<div class="abs photo-frame"></div>
<div class="abs photo" role="img" aria-label="Portrait photo of Joel Brandt"></div>
<section class="abs about">
  <h2>Who am I, what I do,<br>my experience</h2>
  <p class="lead">Demonstrate experience and progression from Scrum Master to Program Manager to Coach</p>
  <p>Joel Brandt is the Owner of Steadfast Delivery Partners, LLC and serves as Principal Lead Consultant on waterfall and agile contract opportunities.</p>
  <p>Steadfast Delivery Partners, LLC has engaged on a contract basis with Summit 300 companies across various industries including banking and credit unions, global supply chain, and international food distribution. Joel Brandt brings 12 years of experience to his clients encompassing various project methodologies including: waterfall, agile, and hybrid frameworks.</p>
  <div class="signature">
    <strong>Joel Brandt</strong>
    <span>Senior Scrum Master &amp; Team Agile Coach</span>
  </div>
</section>

<!-- designations -->
<h2 class="section-title" style="top:1408px">Coaching Designations</h2>
<div class="abs badges">
  <div class="cell"><svg viewBox="0 0 132 124"><circle cx="66" cy="62" r="56" fill="#1e8fe0"/><circle cx="66" cy="62" r="44" fill="none" stroke="#fff" stroke-width="3"/></svg></div>
  <div class="cell"><svg viewBox="0 0 132 124"><circle cx="66" cy="62" r="56" fill="#f29a2e"/><rect x="4" y="50" width="124" height="24" fill="#e5781f"/></svg></div>
  <div class="cell"><svg viewBox="0 0 132 124"><polygon points="66,6 116,34 116,90 66,118 16,90 16,34" fill="#fff" stroke="#0d2a4e" stroke-width="7"/></svg></div>
  <div class="cell"><svg viewBox="0 0 132 124"><polygon points="66,2 128,62 66,122 4,62" fill="#1d2b3c"/><polygon points="66,14 116,62 66,110 16,62" fill="none" stroke="#8a96a6" stroke-width="3"/></svg></div>
  <div class="cell"><svg viewBox="0 0 132 124"><circle cx="66" cy="62" r="56" fill="#f2b11f"/><circle cx="66" cy="62" r="44" fill="none" stroke="#fff" stroke-width="3"/></svg></div>
</div>

<div class="abs profiles">
  <div class="profile">
    <h3><svg viewBox="0 0 15 15"><rect width="15" height="15" rx="2" fill="#1579c8"/><path d="M3.5 7.5l2.5 2.5 5-5" fill="none" stroke="#fff" stroke-width="2"/></svg>Scrum Guild Profile</h3>
    <a>https://www.scrumguild.example/<br>community/profile/jbrandt10</a>
  </div>
  <div class="profile">
    <h3><svg viewBox="0 0 15 15"><rect width="15" height="15" rx="2" fill="#1579c8"/><path d="M3.5 7.5l2.5 2.5 5-5" fill="none" stroke="#fff" stroke-width="2"/></svg>Badgeway Profile</h3>
    <a>https://www.badgeway.example/users/<br>joel-brandt.b71c3d9e</a>
  </div>
  <div class="profile">
    <h3><svg viewBox="0 0 15 15"><rect width="15" height="15" rx="2" fill="#1579c8"/><path d="M3.5 7.5l2.5 2.5 5-5" fill="none" stroke="#fff" stroke-width="2"/></svg>LIMBr Scaled Guild Profile</h3>
    <a>https://community.limbrguild.example/s/<br>profile/00K7Q000041abzTRW</a>
  </div>
</div>

<!-- roles -->
<h2 class="section-title" style="top:1877px">Roles I have held:</h2>
<div class="abs roles">
  <span class="vline"></span>
  <span class="hline"></span>
  <div class="role" style="left:6px;top:0"><svg><use href="#ico-laptop"/></svg>Sr. Scrum Master</div>
  <div class="role" style="left:330px;top:0"><svg><use href="#ico-laptop"/></svg>Advanced LIMBr Scrum<br>Master</div>
  <div class="role" style="left:6px;top:97px"><svg><use href="#ico-laptop"/></svg>Hybrid Scrum Master/<br>Project Manager</div>
  <div class="role" style="left:330px;top:97px"><svg><use href="#ico-laptop"/></svg>Business (Finance<br>Transformation Program<br>Manager)</div>
</div>

<!-- experience -->
<svg class="abs exp-band" viewBox="0 2180 1200 1160">
  <polygon points="0,2282 96,2282 139,2213 1200,2213 1200,3262 1107,3262 1064,3331 0,3331" fill="#12488c"/>
  <polyline points="1072,2216 1112,2189 1200,2189" fill="none" stroke="#1e8fe0" stroke-width="11"/>
</svg>
<h2 class="section-title exp-title">What is my experience</h2>

<article class="card" style="left:93px">
  <div class="card-body"></div>
  <svg class="card-hex" viewBox="0 0 116 120"><polyline points="2,30 58,2 114,30" fill="none" stroke="#fff" stroke-width="3"/><polygon points="58,12 108,38 108,92 58,118 8,92 8,38" fill="#1579c8"/><rect x="42" y="48" width="32" height="22" fill="none" stroke="#fff" stroke-width="3"/><path d="M36 78h44" stroke="#fff" stroke-width="3"/></svg>
  <h3>As a LIMBr Adv Scrum<br>Master, I:</h3>
  <ul>
    <li><svg><use href="#ico-laptop"/></svg>Stand up teams</li>
    <li><svg><use href="#ico-laptop"/></svg>Run development efforts concurrently leading multiple teams</li>
    <li><svg><use href="#ico-laptop"/></svg>Run LIMBr ceremonies</li>
    <li><svg><use href="#ico-laptop"/></svg>Scrum of Scrums facilitator</li>
    <li><svg><use href="#ico-laptop"/></svg>PI Planning team facilitator (multiple teams on ART)</li>
    <li><svg><use href="#ico-laptop"/></svg>Teach and coach to advanced development team strategies</li>
    <li><svg><use href="#ico-laptop"/></svg>Lead program level communications and business status updates on behalf of the team</li>
  </ul>
</article>

<article class="card" style="left:441px">
  <div class="card-body"></div>
  <svg class="card-hex" viewBox="0 0 116 120"><polyline points="2,30 58,2 114,30" fill="none" stroke="#fff" stroke-width="3"/><polygon points="58,12 108,38 108,92 58,118 8,92 8,38" fill="#1579c8"/><rect x="42" y="48" width="32" height="22" fill="none" stroke="#fff" stroke-width="3"/><path d="M36 78h44" stroke="#fff" stroke-width="3"/></svg>
  <h3>As a Hybrid Scrum Master /<br>Project Manager, I:</h3>
  <ul>
    <li><svg><use href="#ico-laptop"/></svg>Standup teams</li>
    <li><svg><use href="#ico-laptop"/></svg>Run multiple program level projects simultaneously</li>
    <li><svg><use href="#ico-laptop"/></svg>Implement custom hybrid development strategies</li>
    <li><svg><use href="#ico-laptop"/></svg>Manage to project triple constraints</li>
    <li><svg><use href="#ico-laptop"/></svg>Communications lead and business liaison</li>
    <li><svg><use href="#ico-laptop"/></svg>Use multiple coaching styles based on team and project</li>
  </ul>
</article>

<article class="card" style="left:790px">
  <div class="card-body"></div>
  <svg class="card-hex" viewBox="0 0 116 120"><polyline points="2,30 58,2 114,30" fill="none" stroke="#fff" stroke-width="3"/><polygon points="58,12 108,38 108,92 58,118 8,92 8,38" fill="#1579c8"/><rect x="42" y="48" width="32" height="22" fill="none" stroke="#fff" stroke-width="3"/><path d="M36 78h44" stroke="#fff" stroke-width="3"/></svg>
  <h3>Business Transformation<br>Program Manager</h3>
  <ul>
    <li><svg><use href="#ico-laptop"/></svg>Lead business transformation efforts at the program level</li>
    <li><svg><use href="#ico-laptop"/></svg>Work with multiple product owners, business analysts, and business stakeholders on requirements</li>
    <li><svg><use href="#ico-laptop"/></svg>Lead the international rollout, onboarding, and support of new transformational CRM tool, Cloudline</li>
    <li><svg><use href="#ico-laptop"/></svg>standup and lead multi-functional teams consisting of business and technology team members</li>
    <li><svg><use href="#ico-laptop"/></svg>Serve as program organization and communications lead</li>
  </ul>
</article>

<!-- cta -->
<div class="abs cta"><h2>Where does coaching<br>come in to play</h2></div>
<a class="abs btn cta-btn">Get in touch <svg><use href="#ico-arrow"/></svg></a>

<!-- footer -->
<svg class="abs footer-bg" viewBox="0 3500 1200 472">
  <polygon points="0,3580 78,3580 120,3528 1200,3528 1200,3972 0,3972" fill="#ececee"/>
  <polygon points="1062,3520 1200,3520 1200,3618 1108,3618" fill="#ffffff"/>
  <polyline points="0,3578 76,3578 118,3524 1058,3524" fill="none" stroke="#1e8fe0" stroke-width="12"/>
</svg>
<div class="abs brand footer-brand"><span class="brand-mark"></span>Q's &amp; V's</div>
<div class="abs social-label">Social Media: <span></span><span></span><span></span></div>
<p class="abs copy">Copyright © 2022 Q's &amp; V's.<br>All rights reserved.</p>

<div class="abs foot-col sitemap">
  <h4>Sitemap</h4>
  <ul>
    <li>Who am I</li>
    <li>Q's &amp; V's</li>
    <li>The Team Level</li>
    <li>The Program Level</li>
    <li>Presentations</li>
    <li>Monthly Blog</li>
  </ul>
</div>

<div class="abs foot-col contacts">
  <h4>Contact us</h4>
  <div class="row"><svg viewBox="0 0 16 16"><path d="M8 1a5 5 0 0 1 5 5c0 4-5 9-5 9S3 10 3 6a5 5 0 0 1 5-5z" fill="#1579c8"/><circle cx="8" cy="6" r="2" fill="#ececee"/></svg>Consectetur adipiscing elit sed do tempor incididunt ut</div>
  <div class="row"><svg viewBox="0 0 16 16"><path d="M3 1l3 1 1 3-2 1.5c1 2 2.5 3.5 4.5 4.5L11 9l3 1 1 3-2 2C7 15 1 9 1 3z" fill="#1579c8"/></svg>555-210-4478</div>
  <div class="row"><svg viewBox="0 0 16 16"><rect x="1" y="3" width="14" height="10" rx="1" fill="#1579c8"/><path d="M1 4l7 5 7-5" fill="none" stroke="#ececee" stroke-width="1.4"/></svg>qsandvs@mail.example</div>
</div>

</body>
</html>
```